SOLVE Study flyer

I need help designing a flyer for a research study that will include brain imaging in adolescents. The info is in the attached document. The study is called the Sequoia Outlook Lantern Valley Echo (SOLVE) study. Ideally this would be returned as a document that I can edit in the future as we will have several new recruitment phases (different age groups, etc. I also would love to have a logo designed as part of this project, but I recognize that might be a separate design request.

```html
<!DOCTYPE html>
<html lang="en">
<head>
<meta charset="utf-8">
<title>SOLVE Study Flyer</title>
<link href="https://fonts.googleapis.com/css2?family=Poppins:wght@400;500;600;700;800&display=swap" rel="stylesheet">
<style>
  :root {
    --navy: #2e2768;
    --purple: #7a52b8;
    --lilac: #a88ad8;
    --lavender-bg: #f2eff8;
    --yellow: #f3c232;
    --ink: #4a4a55;
    --page: #dcdcdc;
    --paper: #ffffff;
  }
  * { box-sizing: border-box; margin: 0; padding: 0; }
  html, body { width: 1200px; height: 900px; overflow: hidden; }
  body { background: var(--page); font-family: "Poppins", sans-serif; color: var(--ink); }

  .flyer {
    position: absolute; left: 270px; top: 23px;
    width: 660px; height: 854px;
    background: var(--paper); overflow: hidden;
    box-shadow: 0 10px 30px rgba(0,0,0,.12);
  }

  /* Brand block */
  .brand { position: absolute; left: 150px; top: 30px; display: flex; align-items: flex-start; gap: 22px; }
  .brand-dot { width: 88px; height: 88px; border-radius: 50%; background: var(--lilac); }
  .brand-name { font-size: 62px; font-weight: 500; color: var(--navy); line-height: 1; letter-spacing: 2px; }
  .brand-sub {
    margin-top: 8px; font-size: 11px; font-weight: 500; color: var(--navy);
    letter-spacing: 1.5px; text-transform: uppercase; line-height: 1.35;
    border-top: 2px solid var(--yellow); border-bottom: 2px solid var(--yellow);
    padding: 4px 0; width: 250px;
  }

  /* Headline */
  .headline { position: absolute; left: 38px; top: 168px; width: 360px; font-weight: 700; font-size: 25px; line-height: 1.22; }
  .headline .ask { color: var(--navy); }
  .headline .worry { color: var(--purple); }
  .headline-rule { position: absolute; left: 38px; top: 300px; width: 60px; height: 4px; background: var(--yellow); border-radius: 2px; }
  .intro { position: absolute; left: 38px; top: 314px; width: 340px; font-size: 12px; line-height: 1.55; }
  .intro strong { color: var(--purple); font-weight: 600; }

  /* Photo panel */
  .photo-panel { position: absolute; left: 390px; top: 190px; width: 270px; height: 370px; }
  .photo {
    position: absolute; left: 30px; top: 30px; width: 220px; height: 340px; border-radius: 110px 20px 0 0;
    background: linear-gradient(170deg, #c79a78 0%, #b98fd9 45%, #9a72cc 100%);
  }

  /* Info cards */
  .card { position: absolute; background: var(--lavender-bg); border-radius: 18px; }
  .card-badge {
    position: absolute; left: -14px; top: -22px; width: 46px; height: 46px; border-radius: 50%;
    background: var(--paper); border: 3px solid var(--purple); display: flex; align-items: center; justify-content: center;
  }
  .card-title { font-size: 12.5px; font-weight: 600; color: var(--purple); letter-spacing: 1px; text-transform: uppercase; line-height: 1.3; }

  .participation { left: 30px; top: 420px; width: 340px; padding: 20px 22px 14px 44px; }
  .step { display: flex; gap: 14px; align-items: flex-start; margin-top: 12px; padding-bottom: 10px; border-bottom: 1px solid #ddd6ea; }
  .step:last-child { border-bottom: none; padding-bottom: 0; }
  .step-icon { flex: 0 0 40px; height: 40px; border-radius: 50%; background: var(--lilac); display: flex; align-items: center; justify-content: center; margin-left: -30px; }
  .step-head { font-size: 12.5px; font-weight: 600; color: var(--purple); line-height: 1.25; }
  .step-text { font-size: 10.5px; line-height: 1.35; color: var(--purple); }

  .eligibility { left: 390px; top: 500px; width: 250px; padding: 22px 18px 14px 26px; }
  .criterion { display: flex; gap: 10px; align-items: flex-start; margin-top: 9px; font-size: 11px; color: var(--navy); line-height: 1.3; }
  .criterion svg { flex: 0 0 16px; }
  .criterion strong { color: var(--purple); font-weight: 600; }
  .criterion .age { font-size: 22px; font-weight: 700; color: var(--purple); line-height: 1; }

  /* Bottom band */
  .contact-band { position: absolute; left: 0; top: 728px; width: 660px; height: 80px; background: var(--navy); display: flex; align-items: center; padding: 0 26px; }
  .band-icon { flex: 0 0 48px; height: 48px; border-radius: 50%; background: var(--lilac); display: flex; align-items: center; justify-content: center; }
  .contact { display: flex; gap: 14px; align-items: center; width: 330px; }
  .contact-title { font-size: 11px; font-weight: 600; color: var(--yellow); letter-spacing: .8px; }
  .contact-text { font-size: 10px; color: #fff; line-height: 1.3; }
  .email-pill { display: inline-block; margin-top: 4px; background: var(--yellow); color: var(--navy); font-size: 10.5px; font-weight: 600; padding: 2px 14px; border-radius: 12px; }
  .band-divider { width: 1px; height: 50px; background: rgba(255,255,255,.35); margin: 0 26px; }
  .compensation { display: flex; gap: 14px; align-items: center; }
  .comp-label { font-size: 11px; font-weight: 600; color: var(--yellow); letter-spacing: .8px; line-height: 1.2; }
  .comp-label small { display: block; font-size: 8px; color: #fff; font-weight: 400; }
  .comp-amount { font-size: 32px; font-weight: 800; color: var(--yellow); line-height: 1; }

  .footer { position: absolute; left: 0; top: 808px; width: 660px; height: 46px; display: flex; align-items: center; padding-left: 40px; gap: 10px; }
  .footer-square { width: 22px; height: 22px; background: var(--navy); }
  .footer-name { font-size: 15px; font-weight: 600; color: var(--navy); }
</style>
</head>
<body>
<main class="flyer">

  <header class="brand">
    <div class="brand-dot"></div>
    <div>
      <div class="brand-name">SOLVE</div>
      <div class="brand-sub">Sequoia Outlook Lantern<br>Valley Echo Study</div>
    </div>
  </header>

  <h1 class="headline">
    <span class="ask">Are you the parent of a child age 10–17?</span><br>
    <span class="worry">Do they worry or overthink negative emotions?</span>
  </h1>
  <div class="headline-rule"></div>
  <p class="intro">Northvale University researchers are seeking <strong>girls age 10–17</strong> for a study about brain activity in emotions and decision-making and how they relate to puberty, anxiety and depression.</p>

  <div class="photo-panel">
    <svg width="270" height="370" viewBox="0 0 270 370" aria-hidden="true">
      <path d="M270 0 L270 370 L0 370 C10 200 90 40 270 0 Z" fill="var(--navy)"/>
      <path d="M270 0 C110 30 20 170 4 340" fill="none" stroke="var(--lilac)" stroke-width="10"/>
    </svg>
    <div class="photo" role="img" aria-label="Photo of a thoughtful teenage girl in a purple sweater looking upward"></div>
  </div>

  <section class="card participation">
    <div class="card-badge">
      <svg width="24" height="24" viewBox="0 0 24 24" aria-hidden="true"><circle cx="12" cy="7" r="4" fill="var(--navy)"/><path d="M3 20 Q12 13 21 20 L21 22 L3 22 Z" fill="var(--navy)"/></svg>
    </div>
    <h2 class="card-title">Study participation involves:</h2>
    <div class="step">
      <div class="step-icon"><svg width="20" height="20" viewBox="0 0 20 20" aria-hidden="true"><rect x="2" y="3" width="16" height="11" rx="2" fill="none" stroke="#fff" stroke-width="1.6"/><path d="M6 14 L6 18 L10 14" fill="none" stroke="#fff" stroke-width="1.6"/></svg></div>
      <div><div class="step-head">One one-hour interview</div><div class="step-text">(online or in-person) where your child will discuss their thoughts</div></div>
    </div>
    <div class="step">
      <div class="step-icon"><svg width="20" height="20" viewBox="0 0 20 20" aria-hidden="true"><rect x="4" y="2" width="12" height="16" rx="1.5" fill="none" stroke="#fff" stroke-width="1.6"/><path d="M7 7 H13 M7 10 H13 M7 13 H11" stroke="#fff" stroke-width="1.4"/></svg></div>
      <div><div class="step-head">Online questionnaires</div><div class="step-text">(parent and child)</div></div>
    </div>
    <div class="step">
      <div class="step-icon"><svg width="20" height="20" viewBox="0 0 20 20" aria-hidden="true"><circle cx="10" cy="10" r="7" fill="none" stroke="#fff" stroke-width="1.6"/><circle cx="10" cy="10" r="3" fill="none" stroke="#fff" stroke-width="1.6"/></svg></div>
      <div><div class="step-head">One two-hour visit</div><div class="step-text">where your child will complete an MRI scan, answer questions about their puberty stage, and have a small hair sample taken to study puberty hormones</div></div>
    </div>
  </section>

  <section class="card eligibility">
    <div class="card-badge" style="background:var(--navy);border-color:var(--navy)">
      <svg width="20" height="20" viewBox="0 0 20 20" aria-hidden="true"><circle cx="10" cy="10" r="5" fill="#fff"/></svg>
    </div>
    <h2 class="card-title">Your child may be eligible if they:</h2>
    <div class="criterion">
      <svg width="16" height="16" viewBox="0 0 16 16" aria-hidden="true"><circle cx="8" cy="8" r="6.5" fill="none" stroke="var(--yellow)" stroke-width="1.5"/><path d="M5 8 L7.3 10.2 L11 5.8" fill="none" stroke="var(--yellow)" stroke-width="1.6"/></svg>
      <div>Are age<br><span class="age">10–17</span></div>
    </div>
    <div class="criterion">
      <svg width="16" height="16" viewBox="0 0 16 16" aria-hidden="true"><circle cx="8" cy="8" r="6.5" fill="none" stroke="var(--yellow)" stroke-width="1.5"/><path d="M5 8 L7.3 10.2 L11 5.8" fill="none" stroke="var(--yellow)" stroke-width="1.6"/></svg>
      <div>Tend to <strong>worry or overthink</strong> negative thoughts</div>
    </div>
    <div class="criterion">
      <svg width="16" height="16" viewBox="0 0 16 16" aria-hidden="true"><circle cx="8" cy="8" r="6.5" fill="none" stroke="var(--yellow)" stroke-width="1.5"/><path d="M5 8 L7.3 10.2 L11 5.8" fill="none" stroke="var(--yellow)" stroke-width="1.6"/></svg>
      <div>Have not been diagnosed with psychosis, learning problems, or autism</div>
    </div>
  </section>

  <section class="contact-band">
    <div class="contact">
      <div class="band-icon"><svg width="26" height="20" viewBox="0 0 26 20" aria-hidden="true"><rect x="1" y="1" width="24" height="18" rx="2" fill="none" stroke="#fff" stroke-width="1.8"/><path d="M1 2 L13 11 L25 2" fill="none" stroke="#fff" stroke-width="1.8"/></svg></div>
      <div>
        <div class="contact-title">INTERESTED IN PARTICIPATING?</div>
        <div class="contact-text">Want more information? Please contact us!</div>
        <span class="email-pill">solvestudy@northvale.edu</span>
      </div>
    </div>
    <div class="band-divider"></div>
    <div class="compensation">
      <div class="band-icon"><svg width="24" height="22" viewBox="0 0 24 22" aria-hidden="true"><rect x="2" y="8" width="20" height="13" fill="none" stroke="#fff" stroke-width="1.8"/><rect x="1" y="4" width="22" height="4" fill="none" stroke="#fff" stroke-width="1.8"/><path d="M12 4 V21" stroke="#fff" stroke-width="1.8"/></svg></div>
      <div>
        <div class="comp-label">COMPENSATION<small>UP TO</small></div>
        <div class="comp-amount">$140</div>
      </div>
    </div>
  </section>

  <footer class="footer">
    <div class="footer-square"></div>
    <span class="footer-name">Northvale University</span>
  </footer>

</main>
</body>
</html>
```